Wordpress website design for children’s entertainment agency

What is the aim of the website?

The aim for the website is to attract potential bookers and to get them to respond to the Call to action: contact the entertainer - phone call/request a call back/completing a form.
All the information needs to be easy to access and navigate to, especially on mobile view.
The call to action needs to be clear and easy to navigate.

What I need:

Critical - This website needs to look good on all devices.
Easy navigation on a mobile device is essential so the elements need to be bold and easy to click on with a thumb (when in mobile view)

The ‘grid area’ needs to be graphics based with simple descriptions, i.e. ‘magic shows’, Circus Clowns, Face painting, Costume Characters, Party Host, Carnival Parties, Balloon Sculpting, DJ and MC, Princess Parties, Holiday Parties, Fun Add Ons and Contact.

See: http://www.jollymarvin.com/
and http://playtimebookingnest.com/

I would like to see a sample page layout as well to see how your design would be carried through the site layout in the inside pages.

Target Market(s)

The site visitors are mainly mums, aged between 25 - 41. Other visitors will included event organisers looking for entertainment services for baptism, communions and sweet 16’s

Industry/Entity Type

Entertainment Industry

Number of Pages Required

1 page

Font styles to use
Sans Serif

Colors
6c459b
fbed22
0493ce

Requirements
Must have
• Critical - This website needs to look good on all devices.
• Easy navigation on a mobile device is essential so the elements need to be bold and easy to click on with a thumb (when in mobile view)
• The ‘grid area’ needs to be graphics based with simple descriptions, i.e. ‘magic shows’, Circus Clowns, Face painting, Costume Characters, Party Host, Carnival Parties, Balloon Sculpting, DJ and MC, Princess Parties, Holiday Parties, Fun Add Ons and Contact.
• See: http://www.jollymarvin.com/
• and http://playtimebookingnest.com/
Nice to have
• clean looking and fun with an element of ‘Trobel’ and stars (this is the exciting site http://gordysjoyshack.com/index.html)

```html
<!DOCTYPE html>
<html lang="en">
<head>
<meta charset="utf-8">
<title>Gordy's Joy Shack – The Children's Entertainer</title>
<link href="https://fonts.googleapis.com/css2?family=Fredoka:wght@500;600&family=Fredoka+One&family=Roboto:wght@400;500&display=swap" rel="stylesheet">
<style>
:root{
  --purple:#6c459b;
  --purple-dark:#4f2f7c;
  --yellow:#fbed22;
  --yellow-deep:#f2c40f;
  --blue:#0493ce;
  --blue-light:#3fb8ea;
  --blue-dark:#0a6fb0;
  --red:#e4141b;
  --ink:#3a2a18;
  --text:#4a4a4a;
  --white:#ffffff;
  --display:'Fredoka One','Fredoka','Arial Rounded MT Bold',sans-serif;
}
*{box-sizing:border-box;margin:0;padding:0}
html,body{width:1200px;height:2439px;overflow:hidden}
body{position:relative;font-family:'Roboto',Arial,sans-serif;background:var(--blue);color:var(--text)}

/* hero */
.hero{position:absolute;left:0;top:0;width:1200px;height:485px;overflow:hidden;
  background:
    radial-gradient(circle at 32% 48%,rgba(255,255,255,.55) 0%,rgba(255,255,255,0) 32%),
    radial-gradient(circle at 40% 40%,#8edcfa 0%,#3db4e8 42%,#0b84ca 100%)}
.hero-photo{position:absolute;left:440px;top:0;width:700px;height:485px;
  background:
    radial-gradient(ellipse 90px 60px at 22% 14%,#d8141b 0%,rgba(216,20,27,0) 100%),
    radial-gradient(ellipse 90px 60px at 52% 10%,#d8141b 0%,rgba(216,20,27,0) 100%),
    radial-gradient(ellipse 80px 55px at 84% 20%,#d8141b 0%,rgba(216,20,27,0) 100%),
    repeating-linear-gradient(90deg,rgba(230,40,40,.75) 0 26px,rgba(250,200,40,.75) 26px 52px),
    linear-gradient(180deg,#2e62c8 0%,#c82a2a 50%,#2a3fa8 100%);
  -webkit-mask:linear-gradient(180deg,transparent 0%,#000 18%,#000 100%);
          mask:linear-gradient(180deg,transparent 0%,#000 18%,#000 100%);opacity:.92}
.brand{position:absolute;left:78px;top:86px;display:flex;align-items:center;gap:14px}
.brand-dot{width:58px;height:58px;border-radius:50%;background:var(--yellow)}
.brand-name{font-family:var(--display);font-size:40px;line-height:42px;color:var(--red);width:230px}
.hero-title{position:absolute;left:78px;top:234px;font-family:var(--display);font-weight:600;
  font-size:50px;line-height:50px;color:var(--red);letter-spacing:1.5px;
  -webkit-text-stroke:7px var(--white);paint-order:stroke fill}
.hero-dots{position:absolute;left:76px;top:432px;display:flex;gap:8px}
.hero-dots span{width:13px;height:13px;border-radius:50%;background:var(--white)}
.hero-dots span.active{background:var(--purple)}
.cloud{position:absolute;display:flex;align-items:center;justify-content:center;
  font-family:var(--display);color:var(--purple);z-index:1}
.cloud svg{position:absolute;inset:0;width:100%;height:100%;z-index:-1;filter:drop-shadow(0 3px 4px rgba(0,0,0,.25))}
.cloud-phone{left:896px;top:40px;width:232px;height:96px;font-size:28px}
.cloud-contact{left:896px;top:404px;width:232px;height:82px;font-size:27px}

/* nav */
.main-nav{position:absolute;left:0;top:485px;width:1200px;height:79px;
  background:linear-gradient(180deg,#fff56a 0%,var(--yellow) 40%,var(--yellow-deep) 100%);
  border-top:3px solid #fff8a8;box-shadow:0 3px 6px rgba(0,0,0,.25)}
.main-nav ul{list-style:none;display:flex;justify-content:space-between;padding:0 78px;height:100%;align-items:center}
.main-nav li{font-family:var(--display);font-size:16px;color:var(--ink);letter-spacing:.8px}

/* purple stage */
.stage{position:absolute;left:0;top:564px;width:1200px;height:1322px;
  background:
    radial-gradient(circle at 8% 12%,rgba(120,190,255,.55) 0%,rgba(120,190,255,0) 18%),
    radial-gradient(circle at 94% 22%,rgba(120,190,255,.5) 0%,rgba(120,190,255,0) 16%),
    radial-gradient(circle at 6% 60%,rgba(140,110,230,.6) 0%,rgba(140,110,230,0) 20%),
    radial-gradient(circle at 96% 70%,rgba(140,110,230,.6) 0%,rgba(140,110,230,0) 20%),
    linear-gradient(180deg,#7a52c2 0%,#5a4cc0 35%,#3d5cc8 70%,#6cc4ee 100%)}
.panel{position:absolute;left:60px;top:589px;width:1078px;height:1297px;background:var(--white);
  border:2px solid #c9c9c9;box-shadow:0 0 10px rgba(0,0,0,.35)}

/* service grid */
.service-grid{position:absolute;left:75px;top:608px;width:782px;display:grid;
  grid-template-columns:repeat(4,192px);gap:6px 4px}
.tile{height:200px;display:flex;flex-direction:column;border-radius:4px;overflow:hidden}
.tile-photo{height:153px}
.tile-label{height:47px;background:var(--blue);color:var(--white);display:flex;align-items:center;justify-content:center;
  font-family:var(--display);font-size:14.5px;letter-spacing:.8px;text-transform:uppercase}

/* welcome */
.welcome{position:absolute;left:75px;top:1249px;width:782px;height:621px;border:1px solid #d5d5d5;border-radius:6px;overflow:hidden;
  box-shadow:0 1px 4px rgba(0,0,0,.15)}
.welcome-head{height:100px;background:var(--yellow);text-align:center;padding-top:20px;font-family:var(--display);color:var(--ink)}
.welcome-head .small{font-size:24px;line-height:26px}
.welcome-head .big{font-size:35px;line-height:42px;letter-spacing:.5px}
.welcome-body{padding:18px 26px;text-align:center;font-size:13.4px;line-height:25.5px;color:var(--text)}
.welcome-body p{margin-bottom:14px}
.welcome-body p.accent{color:var(--purple)}

/* sidebar */
.side-box{position:absolute;left:870px;width:255px;background:var(--purple);border:5px solid var(--white);
  border-radius:48px 48px 60px 60px;box-shadow:0 0 0 3px #c7b4e4,0 3px 8px rgba(0,0,0,.35);text-align:center;font-family:var(--display)}
.side-title{color:var(--yellow);font-size:34px;line-height:37px}
.side-sub{color:var(--white);font-size:20px;line-height:24px}
.quote-box{top:610px;height:483px;padding-top:36px}
.quote-box .side-sub{font-size:19px;margin-bottom:16px}
.field{display:block;margin:0 auto 8px;width:217px;height:36px;background:var(--white);border:1px solid #bdbdbd;border-radius:3px;
  font-family:'Roboto',sans-serif;font-size:13px;color:#777;line-height:34px}
.field.msg{height:82px;line-height:20px;padding-top:8px}
.btn-yellow{display:block;margin:0 auto;background:linear-gradient(180deg,#fff36b,var(--yellow-deep));border-radius:4px;
  font-family:var(--display);color:var(--ink);box-shadow:0 2px 3px rgba(0,0,0,.3);text-align:center}
.quote-box .btn-yellow{width:217px;height:55px;font-size:24px;line-height:55px;margin-top:12px}
.offer-box{top:1114px;height:293px;padding-top:40px}
.offer-box .side-title{font-size:33px;line-height:37px}
.offer-box .btn-yellow{width:217px;height:55px;font-size:23px;line-height:55px;margin-top:12px}
.call-box{top:1431px;height:252px;padding-top:36px}
.call-box .side-title{font-size:32px;line-height:35px}
.call-box .phone{color:var(--white);font-size:29px;margin-top:4px}
.follow-box{top:1704px;height:155px;padding-top:34px}
.social{display:flex;justify-content:center;gap:6px;margin-top:12px}
.social span{width:28px;height:28px;border-radius:50%;background:var(--blue-light);border:2px solid var(--white)}

/* footer */
.footer-scene{position:absolute;left:0;top:1886px;width:1200px;height:455px;
  background:
    radial-gradient(ellipse 300px 90px at 20% 8%,rgba(120,200,90,.55) 0%,rgba(120,200,90,0) 100%),
    radial-gradient(ellipse 300px 90px at 80% 8%,rgba(120,200,90,.55) 0%,rgba(120,200,90,0) 100%),
    linear-gradient(180deg,#5fd0f2 0%,#27a6de 28%,#0b8acc 100%)}
.f-head{position:absolute;top:1996px;font-family:var(--display);font-weight:normal;font-size:25px;color:var(--yellow);letter-spacing:.5px}
.map{position:absolute;left:75px;top:2044px;width:330px;height:239px;background:linear-gradient(135deg,#e8ecd8,#d6dfe6);border:1px solid #c0c0c0}
.f-field{position:absolute;left:434px;width:333px;height:34px;background:var(--white);border-radius:3px;font-size:13px;color:#666;padding:9px 12px}
.f-submit{position:absolute;left:628px;top:2241px;width:138px;height:42px;font-size:17px;line-height:42px}
.quick{position:absolute;top:2038px;list-style:none;font-size:13px;line-height:26px;color:var(--white)}
.f-phone-label{position:absolute;left:818px;top:2218px;font-family:var(--display);font-size:24px;color:var(--yellow);letter-spacing:.5px}
.f-phone{position:absolute;left:818px;top:2250px;font-family:var(--display);font-size:29px;color:var(--white);letter-spacing:.5px}

.bottom-bar{position:absolute;left:0;top:2341px;width:1200px;height:98px;background:var(--blue-dark)}
.bottom-rule{position:absolute;left:75px;top:2328px;width:1050px;height:1px;background:rgba(255,255,255,.45)}
.bottom-nav{position:absolute;left:75px;top:2347px;display:flex;gap:22px;list-style:none;font-size:13px;color:var(--white)}
.copyright{position:absolute;left:75px;top:2372px;font-size:12px;line-height:20px;color:var(--white)}
</style>
</head>
<body>

<header class="hero">
  <div class="hero-photo" role="img" aria-label="Three clowns in red and yellow striped costumes with red hats, one holding a white dove and balloon animals"></div>
  <div class="brand"><span class="brand-dot"></span><span class="brand-name">Gordy's Joy Shack</span></div>
  <h1 class="hero-title">GORDY'S JOY SHACK<br>THE CHILDREN'S<br>ENTERTAINER</h1>
  <div class="hero-dots"><span class="active"></span><span></span><span></span><span></span></div>
  <div class="cloud cloud-phone">
    <svg viewBox="0 0 232 96" preserveAspectRatio="none"><path fill="#fff" d="M30 78 C6 78 4 50 24 44 C18 22 46 12 62 24 C72 6 104 4 116 20 C130 4 164 6 172 24 C194 14 222 26 214 48 C232 56 226 84 200 82 C188 94 160 94 148 84 C132 94 104 94 90 84 C74 94 44 92 30 78 Z"/></svg>
    555-014-2270</div>
  <div class="cloud cloud-contact">
    <svg viewBox="0 0 232 82" preserveAspectRatio="none"><path fill="#fff" d="M28 70 C4 68 6 40 26 38 C22 18 50 10 64 22 C76 4 108 4 118 18 C132 4 166 6 172 22 C196 12 222 24 214 44 C232 52 224 78 198 74 C184 84 156 84 144 76 C128 84 100 84 88 76 C70 84 40 82 28 70 Z"/></svg>
    CONTACT US</div>
</header>

<nav class="main-nav">
  <ul>
    <li>HOME</li><li>ABOUT</li><li>AREAS COVERED</li><li>SEVICES</li><li>TESTIMONIALS</li><li>CONTACT</li><li>FUN STUFF</li>
  </ul>
</nav>

<div class="stage" role="img" aria-label="Purple and blue background scattered with outlined stars"></div>
<main class="panel"></main>

<section class="service-grid">
  <div class="tile"><div class="tile-photo" role="img" aria-label="Magician performing for children" style="background:linear-gradient(160deg,#9fc0e0 0%,#d22a36 55%,#8a1a24 100%)"></div><div class="tile-label">Magic Shows</div></div>
  <div class="tile"><div class="tile-photo" role="img" aria-label="Circus clowns on a stage" style="background:linear-gradient(160deg,#f0b840 0%,#e0402c 55%,#3d7a3a 100%)"></div><div class="tile-label">Circus Clowns</div></div>
  <div class="tile"><div class="tile-photo" role="img" aria-label="Child with face paint" style="background:linear-gradient(160deg,#e05040 0%,#c84a4a 45%,#3a2424 100%)"></div><div class="tile-label">Face Painting</div></div>
  <div class="tile"><div class="tile-photo" role="img" aria-label="Children in costumes" style="background:linear-gradient(160deg,#e8c080 0%,#c24a2a 55%,#5a3a22 100%)"></div><div class="tile-label">Costume Characters</div></div>
  <div class="tile"><div class="tile-photo" role="img" aria-label="Party host with a puppet" style="background:linear-gradient(160deg,#f4ece2 0%,#e06a30 55%,#2a2a3a 100%)"></div><div class="tile-label">Party Host</div></div>
  <div class="tile"><div class="tile-photo" role="img" aria-label="Carnival game stalls outdoors" style="background:linear-gradient(160deg,#8fc45a 0%,#d84a3a 60%,#f0f0f0 100%)"></div><div class="tile-label">Carnival Parties</div></div>
  <div class="tile"><div class="tile-photo" role="img" aria-label="Balloon sculptures" style="background:linear-gradient(160deg,#dfe2ea 0%,#d8344a 50%,#3a5cc8 100%)"></div><div class="tile-label">Balloon Sculpting</div></div>
  <div class="tile"><div class="tile-photo" role="img" aria-label="Colourful party lights" style="background:linear-gradient(160deg,#142c6a 0%,#2e8ad8 45%,#38e06a 100%)"></div><div class="tile-label">DJ and MC</div></div>
  <div class="tile"><div class="tile-photo" role="img" aria-label="Girls in princess dresses dancing" style="background:linear-gradient(160deg,#8fc45a 0%,#f0a8c8 55%,#c878d8 100%)"></div><div class="tile-label">Princess Parties</div></div>
  <div class="tile"><div class="tile-photo" role="img" aria-label="Costumed bunny character" style="background:linear-gradient(160deg,#6fa84a 0%,#f4f2f0 50%,#e8a0b0 100%)"></div><div class="tile-label">Holiday Parties</div></div>
  <div class="tile"><div class="tile-photo" role="img" aria-label="Entertainer in a patriotic costume" style="background:linear-gradient(160deg,#d8343c 0%,#f2f2f2 45%,#2448a8 100%)"></div><div class="tile-label">Fun Add Ons</div></div>
  <div class="tile"><div class="tile-photo" role="img" aria-label="Child on a phone" style="background:linear-gradient(160deg,#f2f2f4 0%,#c8a890 45%,#22242a 100%)"></div><div class="tile-label">Contact Us</div></div>
</section>

<section class="welcome">
  <div class="welcome-head"><div class="small">WELCOME TO</div><div class="big">GORDY'S JOY SHACK ENTERTAINMENT</div></div>
  <div class="welcome-body">
    <p>Have you ever heard the expression "make your own fun"? Well, when you call Gordy's Joy Shack, you don't have to! We make all the fun you'll need, and bring it straight to you. Clowns, Magicians, Face Painting, Balloon Animals, Jugglers, Party Princesses, Carnivals and much more, we create all of the fun that anyone could ever want! Our children's party entertainers appeal to your sense of fun regardless of age and we have a wide range of party services .Yes, We can come to your back yard party, catering hall, restaurant, Birthday party, communion, sweet sixteen's, christenings, baptism, bar mitzvah, bat mitzvah We service New York: Staten Island, NY, Brooklyn, NY, NYC and New Jersey, We guaranteed to make your party or special event a memorable one!</p>
    <p class="accent">Aliquam molestie, mi et imperdiet euismod, dui purus auctor tellus, et interdum lacus lectus et ante. Sed accumsan sollicitudin sapien, sit amet adipiscing turpis gravida ac. In congue, neque ac lobortis volutpat, libero mauris varius mi, vitae suscipit ipsum ligula vitae risus. Duis aliquam nibh a dui iaculis viverra id a velit. Vivamus egestas risus in magna varius commodo. Sed semper viverra egestas.</p>
    <p>Have you ever heard the expression "make your own fun"? Well, when you call Gordy's Joy Shack, you don't have to! We make all the fun you'll need, and bring it straight to you. Clowns, Magicians, Face Painting, Balloon Animals, Jugglers, Party Princesses, Carnivals and much more, we create all of the fun that anyone could ever want! Our children's party entertainers appeal to your sense of fun regardless of age and we have a wide range of party services .Yes, We can come to your back yard party, catering hall, restaurant, Birthday party, communion, sweet sixteen's, christenings, baptism, bar mitzvah, bat mitzvah We service New York: Staten Island, NY, Brooklyn, NY, NYC and New Jersey, We guaranteed to make your party or special event a memorable one!</p>
  </div>
</section>

<aside>
  <div class="side-box quote-box">
    <div class="side-title">CONTACT US</div>
    <div class="side-sub">FOR A FREE QUOTE</div>
    <div class="field">Name of Child</div>
    <div class="field">Email Address</div>
    <div class="field">Postal Code</div>
    <div class="field">Phone No.</div>
    <div class="field msg">Message</div>
    <div class="btn-yellow">SUBMIT</div>
  </div>
  <div class="side-box offer-box">
    <div class="side-title">SPECIAL<br>OFFERS</div>
    <div class="side-sub">PAMPER PARTY</div>
    <div class="side-title" style="font-size:26px;line-height:30px">WORTH $340</div>
    <div class="btn-yellow">CLICK HERE</div>
  </div>
  <div class="side-box call-box">
    <div class="side-title">CONTACT<br>THE<br>ENTERTAINER</div>
    <div class="side-sub" style="margin-top:8px">PHONE CALL</div>
    <div class="phone">555-014-2270</div>
  </div>
  <div class="side-box follow-box">
    <div class="side-title">FOLLOW US</div>
    <div class="social"><span></span><span></span><span></span><span></span><span></span><span></span></div>
  </div>
</aside>

<footer>
  <div class="footer-scene" role="img" aria-label="Cartoon park scene with trees, children and toy cars on a blue background"></div>
  <h3 class="f-head" style="left:75px">OUR LOCATION</h3>
  <div class="map" role="img" aria-label="Street map showing the business location"></div>
  <h3 class="f-head" style="left:434px">CONTACT FORM</h3>
  <div class="f-field" style="top:2044px">Full Name</div>
  <div class="f-field" style="top:2084px">Email Address</div>
  <div class="f-field" style="top:2124px">Contact No</div>
  <div class="f-field" style="top:2163px;height:68px">Message</div>
  <div class="btn-yellow f-submit">SUBMIT</div>
  <h3 class="f-head" style="left:818px">QUICK LINKS</h3>
  <ul class="quick" style="left:818px"><li>Magic Shows</li><li>Circus Clowns</li><li>Face Painting</li><li>Costume Characters</li><li>Party Host</li><li>Carnival Parties</li></ul>
  <ul class="quick" style="left:984px"><li>Balloon Sculpting</li><li>DJ and MC</li><li>Princess Parties</li><li>Holiday Parties</li><li>Fun Add Ons</li></ul>
  <div class="f-phone-label">PHONE CALL:</div>
  <div class="f-phone">555-014-2270</div>

  <div class="bottom-bar"></div>
  <div class="bottom-rule"></div>
  <ul class="bottom-nav"><li>Home</li><li>About</li><li>Areas Covered</li><li>Sevices</li><li>Testimonials</li><li>Contact</li><li>Fun stuff</li></ul>
  <div class="copyright">Copyright © 2015 Gordy's Joy Shack Entertainment<br>All Right Reserved &nbsp;|&nbsp; Sitemap | Privacy</div>
</footer>

</body>
</html>
```